Wordpress theme website for professionals working together

My partner and I are offering business services, my wife in the energy business as mainly as member of the board of commissioners. I am working as interim manager/consultant in the accounting and finance area. Both activities are connected in one company VELMOT BV (dutch ltd). We need a CV based website. Beside this we do some financial and accounting services.

Target Market(s)

small medium business

Font styles to use
Sans Serif

Colors

Designer to choose colors to be used in the design.

Requirements
Must have
• Pictures of both members.
• CLEAN AND SIMPLE
• I LIKE BLACK & WHITE
Nice to have
• I like design like this theme: http://theme.pruxelo-example.com/resume/

```html
<!DOCTYPE html>
<html lang="en">
<head>
<meta charset="utf-8">
<title>VELMOT BV – Resume</title>
<link href="https://fonts.googleapis.com/css2?family=Poppins:wght@400;500;600;700&family=Roboto:wght@300;400;500;700&display=swap" rel="stylesheet">
<style>
:root{
  --ink:#1b1b1b;
  --text:#333;
  --muted:#555;
  --light-band:#ececec;
  --white:#fff;
  --header:#1c1c1c;
  --contact:#141414;
  --footer:#0c0c0c;
  --bar-top:#a8a8a8;
  --bar-bottom:#7d7d7d;
  --line:#d6d6d6;
}
*{margin:0;padding:0;box-sizing:border-box}
html,body{width:1200px;height:3930px;overflow:hidden}
body{position:relative;background:var(--white);font-family:"Roboto",Arial,sans-serif;color:var(--text)}
.abs{position:absolute}

/* header */
.site-header{position:absolute;left:0;top:0;width:1200px;height:85px;background:var(--header)}
.brand{position:absolute;left:145px;top:22px;font-family:"Poppins",Arial,sans-serif;font-weight:700;font-size:36px;color:var(--white);letter-spacing:1px}
.main-nav{position:absolute;right:145px;top:34px;display:flex;gap:26px}
.main-nav a{font-family:"Poppins",Arial,sans-serif;font-size:15px;color:var(--white);text-decoration:none;font-weight:500}

/* hero */
.hero{position:absolute;left:0;top:85px;width:1200px;height:593px;background:linear-gradient(90deg,#dfe3e8 0%,#d5d9df 40%,#c7ccd2 55%,#b9b1a8 75%,#6b6a70 100%)}
.hero-photo{position:absolute;left:560px;top:0;width:640px;height:593px;background:radial-gradient(ellipse at 55% 45%,#c9a590 0%,#a88673 35%,rgba(90,90,100,0.2) 70%,rgba(0,0,0,0) 100%)}
.hero h1{position:absolute;left:145px;top:120px;font-size:50px;font-weight:400;color:var(--ink);letter-spacing:1px}
.hero h1 b{font-weight:700}
.hero p{position:absolute;left:145px;top:195px;width:450px;font-size:14px;line-height:26px;color:var(--ink)}
.btn-outline{position:absolute;height:40px;border:2px solid var(--ink);border-radius:20px;font-family:"Poppins",Arial,sans-serif;font-weight:600;font-size:15px;color:var(--ink);display:flex;align-items:center;justify-content:center;gap:7px}

/* section titles */
.section-title{position:absolute;left:0;width:1200px;text-align:center;font-size:40px;font-weight:400;color:var(--ink)}
.section-title b{font-weight:700}
.divider{position:absolute;left:540px;width:120px;height:12px}
.section-title.light{color:var(--white)}

/* skills */
.skill-label{position:absolute;left:150px;width:272px;text-align:right;font-size:18px;color:var(--ink)}
.skill-bar{position:absolute;left:456px;height:20px;background:linear-gradient(var(--bar-top),var(--bar-bottom));box-shadow:0 5px 6px rgba(0,0,0,.25)}
.skill-pct{position:absolute;font-size:20px;font-weight:700;color:var(--ink)}

/* experience */
.band{position:absolute;left:0;width:1200px;background:var(--light-band)}
.exp-card{position:absolute;top:1573px;width:440px;height:257px;background:var(--white);box-shadow:0 2px 8px rgba(0,0,0,.25);overflow:hidden}
.exp-card .wedge{position:absolute;left:0;top:0}
.exp-badge{position:absolute;left:28px;top:68px;width:122px;height:122px;border:3px solid var(--ink);border-radius:50%;background:var(--white);text-align:center}
.exp-badge span{display:block;font-size:18px;font-weight:700;line-height:20px;color:var(--ink)}
.exp-list{position:absolute;left:178px;top:30px;width:245px}
.exp-list h3{font-size:19px;font-weight:500;color:var(--ink)}
.exp-list p{font-size:13px;color:var(--muted);margin:3px 0 14px}
.exp-list p.body{line-height:19px}

/* education */
.timeline{position:absolute;left:145px;top:2365px;width:910px;height:4px;background:var(--line)}
.timeline-done{position:absolute;left:145px;top:2364px;width:95px;height:6px;background:var(--ink)}
.node{position:absolute;width:16px;height:16px;border-radius:50%;background:var(--line);top:2359px}
.node.active{width:20px;height:20px;top:2357px;background:var(--ink)}
.edu-box{position:absolute;width:195px;height:103px;background:var(--white);border-radius:8px;box-shadow:0 3px 10px rgba(0,0,0,.2);text-align:center;padding-top:18px}
.edu-box h4{font-size:19px;font-weight:500;color:var(--ink)}
.edu-box p{font-size:13px;line-height:18px;color:var(--muted);margin-top:6px}
.edu-box.dark{background:#3a3a3a}
.edu-box.dark h4,.edu-box.dark p{color:var(--white)}

/* testimonial */
.avatar{position:absolute;left:549px;top:2724px;width:102px;height:102px;border-radius:50%;background:radial-gradient(circle at 50% 40%,#b69a88,#5c6b7a 70%,#2f3b48)}
.quote-mark{position:absolute;top:2748px;font-family:Georgia,serif;font-size:60px;color:#bdbdbd;line-height:1}
.quote-text{position:absolute;left:170px;top:2850px;width:860px;text-align:center;font-size:15px;line-height:31px;color:var(--muted)}
.quote-author{position:absolute;left:0;top:2962px;width:1200px;text-align:center;font-size:16px;font-weight:700;font-style:italic;color:var(--ink)}
.dots{position:absolute;left:573px;top:3022px;display:flex;gap:6px}
.dots i{width:14px;height:14px;border:2px solid var(--ink);border-radius:50%}

/* contact */
.contact{position:absolute;left:0;top:3098px;width:1200px;height:649px;background:radial-gradient(ellipse at 60% 40%,#242424,var(--contact) 70%)}
.contact-item{position:absolute;left:145px;display:flex;gap:24px;align-items:center;color:var(--white);font-size:17px;line-height:24px}
.contact-icon{width:56px;height:56px;border:3px solid var(--white);border-radius:50%;display:flex;align-items:center;justify-content:center;flex:none}
.field{position:absolute;border:1px solid #cfcfcf;color:var(--white);font-size:14px;padding:9px 14px}
.send-btn{position:absolute;left:463px;top:3605px;width:185px;height:40px;border:2px solid var(--white);border-radius:20px;color:var(--white);font-family:"Poppins",Arial,sans-serif;font-weight:600;font-size:15px;display:flex;align-items:center;justify-content:center}

/* footer */
.site-footer{position:absolute;left:0;top:3747px;width:1200px;height:183px;background:var(--footer)}
.copyright{position:absolute;left:0;top:58px;width:1200px;text-align:center;font-size:14px;color:var(--white)}
.social{position:absolute;left:535px;top:106px;display:flex;gap:8px}
.social i{width:24px;height:24px;border:2px solid var(--white);border-radius:50%}
.to-top{position:absolute;left:1106px;top:60px}
</style>
</head>
<body>

<header class="site-header">
  <div class="brand">VELMOT BV</div>
  <nav class="main-nav">
    <a>HOME</a><a>SKILLS</a><a>EXPERIENCE</a><a>PORTFOLIO</a><a>EDUCATION</a><a>CONTACT</a>
  </nav>
</header>

<section class="hero">
  <div class="hero-photo" role="img" aria-label="Portrait photo of Marten, smiling, wearing glasses"></div>
  <h1><b>ABOUT</b> MARTEN</h1>
  <p>Sed ut perspiciatis unde omnis iste natus error sit voluptatem accusantium doloremque laudantium, totam rem aperiam, eaque ipsa quae ab illo inventore veritatis et quasi architecto beatae vitae dicta sunt explicabo. Nemo enim ipsam voluptatem quia voluptas sit aspernatur aut odit aut fugit, sed quia</p>
  <div class="btn-outline" style="left:145px;top:382px;width:150px">LEARN MORE</div>
  <div class="btn-outline" style="left:312px;top:382px;width:128px">
    <svg width="18" height="18" viewBox="0 0 18 18"><circle cx="9" cy="9" r="8" fill="none" stroke="#1b1b1b" stroke-width="2"/><circle cx="9" cy="7" r="3" fill="#1b1b1b"/><path d="M3.5 14.5c1.5-3 9.5-3 11 0" fill="#1b1b1b"/></svg>ILSE
  </div>
</section>

<!-- skills -->
<h2 class="section-title" style="top:755px"><b>OUR</b> SKILLS</h2>
<svg class="divider" style="top:827px" viewBox="0 0 120 12"><circle cx="6" cy="6" r="4" fill="none" stroke="#1b1b1b" stroke-width="1.5"/><circle cx="114" cy="6" r="4" fill="none" stroke="#1b1b1b" stroke-width="1.5"/><line x1="10" y1="6" x2="110" y2="6" stroke="#1b1b1b" stroke-width="1.5"/><line x1="30" y1="10" x2="90" y2="10" stroke="#1b1b1b" stroke-width="1"/></svg>

<div class="skill-label" style="top:904px">Annual reporting</div><div class="skill-bar" style="top:906px;width:240px"></div><div class="skill-pct" style="left:710px;top:903px">50%</div>
<div class="skill-label" style="top:951px">Financial monthly reporting</div><div class="skill-bar" style="top:953px;width:358px"></div><div class="skill-pct" style="left:827px;top:950px">65%</div>
<div class="skill-label" style="top:998px">Accounting</div><div class="skill-bar" style="top:1000px;width:416px"></div><div class="skill-pct" style="left:887px;top:1000px">70%</div>
<div class="skill-label" style="top:1047px">Financial management</div><div class="skill-bar" style="top:1049px;width:495px"></div><div class="skill-pct" style="left:966px;top:1050px">81%</div>
<div class="skill-label" style="top:1095px">Project management</div><div class="skill-bar" style="top:1097px;width:288px"></div><div class="skill-pct" style="left:759px;top:1097px">57%</div>
<div class="skill-label" style="top:1142px">Team player</div><div class="skill-bar" style="top:1144px;width:495px"></div><div class="skill-pct" style="left:966px;top:1144px">81%</div>
<div class="skill-label" style="top:1190px">Trouble shooter</div><div class="skill-bar" style="top:1192px;width:288px"></div><div class="skill-pct" style="left:759px;top:1192px">57%</div>

<!-- experience -->
<div class="band" style="top:1335px;height:622px"></div>
<h2 class="section-title" style="top:1410px"><b>OUR</b> EXPERIENCE</h2>
<svg class="divider" style="top:1484px" viewBox="0 0 120 12"><circle cx="6" cy="6" r="4" fill="none" stroke="#1b1b1b" stroke-width="1.5"/><circle cx="114" cy="6" r="4" fill="none" stroke="#1b1b1b" stroke-width="1.5"/><line x1="10" y1="6" x2="110" y2="6" stroke="#1b1b1b" stroke-width="1.5"/><line x1="30" y1="10" x2="90" y2="10" stroke="#1b1b1b" stroke-width="1"/></svg>

<article class="exp-card" style="left:145px">
  <svg class="wedge" width="200" height="257"><polygon points="0,0 160,128 0,257" fill="#e9e9e9"/></svg>
  <div class="exp-badge">
    <svg style="margin-top:16px" width="22" height="26" viewBox="0 0 22 26"><path d="M2 1h12l6 6v18H2z" fill="none" stroke="#1b1b1b" stroke-width="2"/><line x1="6" y1="12" x2="16" y2="12" stroke="#1b1b1b" stroke-width="2"/><line x1="6" y1="17" x2="16" y2="17" stroke="#1b1b1b" stroke-width="2"/></svg>
    <span>ACTUAL</span><span>JOBS</span>
  </div>
  <div class="exp-list">
    <h3>Advisor TVL</h3><p>Quis autem vel eum iure repre</p>
    <h3>Advisor How &amp; knower</h3><p>Quis autem vel eum iure repre</p>
    <p class="body">Sed ut perspiciatis unde omnis iste natus error sit voluptatem accusantium doloremque laudantium</p>
  </div>
</article>

<article class="exp-card" style="left:615px">
  <svg class="wedge" width="200" height="257"><polygon points="0,0 160,128 0,257" fill="#e9e9e9"/></svg>
  <div class="exp-badge">
    <svg style="margin-top:16px" width="22" height="26" viewBox="0 0 22 26"><path d="M2 1h12l6 6v18H2z" fill="none" stroke="#1b1b1b" stroke-width="2"/><line x1="6" y1="12" x2="16" y2="12" stroke="#1b1b1b" stroke-width="2"/><line x1="6" y1="17" x2="16" y2="17" stroke="#1b1b1b" stroke-width="2"/></svg>
    <span>FINISHED</span><span>JOBS</span>
  </div>
  <div class="exp-list">
    <h3>Controller a.i. TVL</h3><p>Quis autem vel eum iure repre</p>
    <h3>Advisor Lumen Green</h3><p>Quis autem vel eum iure repre</p>
    <h3>Financial director KRN</h3><p>Quis autem vel eum iure repre</p>
  </div>
</article>

<!-- education -->
<h2 class="section-title" style="top:2047px"><b>OUR</b> EDUCATION</h2>
<svg class="divider" style="top:2117px" viewBox="0 0 120 12"><circle cx="6" cy="6" r="4" fill="none" stroke="#1b1b1b" stroke-width="1.5"/><circle cx="114" cy="6" r="4" fill="none" stroke="#1b1b1b" stroke-width="1.5"/><line x1="10" y1="6" x2="110" y2="6" stroke="#1b1b1b" stroke-width="1.5"/><line x1="30" y1="10" x2="90" y2="10" stroke="#1b1b1b" stroke-width="1"/></svg>

<div class="timeline"></div>
<div class="timeline-done"></div>
<div class="node active" style="left:230px"></div>
<div class="node" style="left:414px"></div>
<div class="node" style="left:597px"></div>
<div class="node" style="left:779px"></div>
<div class="node" style="left:954px"></div>

<div class="edu-box dark" style="left:145px;top:2213px"><h4>Stavra (RA)</h4><p>Sed ut perspiciatis unde<br>omnis iste natus</p></div>
<svg class="abs" style="left:228px;top:2315px" width="24" height="12"><polygon points="0,0 24,0 12,12" fill="#3a3a3a"/></svg>
<div class="edu-box" style="left:503px;top:2213px"><h4>Atheneum B</h4><p>Sed ut perspiciatis<br>iste natus sit</p></div>
<div class="edu-box" style="left:860px;top:2213px"><h4>Manager 2010</h4><p>Sed ut perspiciatis<br>iste natus sit</p></div>
<div class="edu-box" style="left:325px;top:2420px"><h4>Worked for</h4><p>Halvorn Advocaten &amp;<br>Notarissen Dekmor</p></div>
<div class="edu-box" style="left:688px;top:2420px"><h4>Other</h4><p>Fotography<br>iste natus perspiciatis</p></div>

<!-- testimonial -->
<div class="band" style="top:2651px;height:447px"></div>
<div class="quote-mark" style="left:490px">&#8220;</div>
<div class="avatar" role="img" aria-label="Round portrait photo of the client giving the testimonial"></div>
<div class="quote-mark" style="left:672px">&#8221;</div>
<p class="quote-text">Sed ut perspiciatis unde omnis iste natus error sit voluptatem accusantium doloremque laudantium, totam rem aperiam, eaque ipsa quae ab illo inventore veritatis et quasi architecto beatae vitae dicta sunt explicabo. Nemo enim ipsam voluptatem quia voluptas sit aspernatur aut odit aut fugit Sed ut perspiciatis unde omnis iste natus error sit voluptatem</p>
<p class="quote-author">— Blandit Lectus</p>
<div class="dots"><i></i><i></i><i></i></div>

<!-- contact -->
<section class="contact">
  <h2 class="section-title light" style="top:74px"><b>CONTACT</b> US</h2>
</section>
<svg class="divider" style="top:3242px" viewBox="0 0 120 12"><circle cx="6" cy="6" r="4" fill="none" stroke="#fff" stroke-width="1.5"/><circle cx="114" cy="6" r="4" fill="none" stroke="#fff" stroke-width="1.5"/><line x1="10" y1="6" x2="110" y2="6" stroke="#fff" stroke-width="1.5"/><line x1="30" y1="10" x2="90" y2="10" stroke="#fff" stroke-width="1"/></svg>

<div class="contact-item" style="top:3326px">
  <div class="contact-icon"><svg width="18" height="24" viewBox="0 0 18 24"><path d="M9 1a8 8 0 0 0-8 8c0 6 8 14 8 14s8-8 8-14a8 8 0 0 0-8-8z" fill="#fff"/><circle cx="9" cy="9" r="3" fill="#141414"/></svg></div>
  <div>VELMOT BV 1200, Lindenhof<br>Kade, Utrecht</div>
</div>
<div class="contact-item" style="top:3425px">
  <div class="contact-icon"><svg width="20" height="20" viewBox="0 0 20 20"><path d="M4 1l4 4-2 3c1 2 4 5 6 6l3-2 4 4-3 3C9 19 1 11 1 4z" fill="#fff"/></svg></div>
  <div>Phone<br>5550 1234 0000</div>
</div>
<div class="contact-item" style="top:3522px">
  <div class="contact-icon"><svg width="22" height="20" viewBox="0 0 22 20"><path d="M11 1L1 10h3v9h5v-6h4v6h5v-9h3z" fill="#fff"/></svg></div>
  <div>Email<br>info@marten-example.com</div>
</div>

<div class="field" style="left:463px;top:3330px;width:285px;height:38px">Your Name......</div>
<div class="field" style="left:770px;top:3330px;width:285px;height:38px">Email Address....</div>
<div class="field" style="left:463px;top:3395px;width:592px;height:175px">Your Messages.....</div>
<div class="send-btn">SEND MESSAGES</div>

<!-- footer -->
<footer class="site-footer">
  <p class="copyright">VELMOT BV © 2018 All Rights Reserved | Privacy Policy | Terms and Conditions</p>
  <div class="social"><i></i><i></i><i></i><i></i></div>
  <svg class="to-top" width="16" height="14" viewBox="0 0 16 14"><path d="M13 12V4H4M7 1L4 4l3 3" fill="none" stroke="#bbb" stroke-width="1.5"/></svg>
</footer>

</body>
</html>
```